Federal IT Consulting Company - Brisolux Consulting Group

We're seeking a skilled web designer to create a modern, bold, and engaging WordPress website for Brisolux Consulting Group, LLC. Our company specializes in federal IT consulting, and our name is a play on "Brightening Solutions." The website should reflect our expertise in the federal technology marketplace and position us as a trusted partner for clients navigating their IT journey.

contact: info@brisoluxgrp-example.com

Current Status

WordPress is already installed on our hosting account
We have an existing logo (may need modernization)

Design Requirements

Style:

Modern and visually striking design
Bold elements to convey confidence and expertise
Incorporate the concept of "brightening solutions" into the design

Features:

Modern UX sliders for dynamic content presentation
Eye-catching, high-quality images (stock photos to be sourced by the designer)
Responsive design for all devices

Color Scheme:

To be proposed by the designer, should align with our brand and convey trust and technological expertise

Logo:

Evaluate our current logo
Create a transparent background version if needed
Propose modernization if deemed necessary

Accessibility:

Ensure design elements are accessible to users with disabilities
Use high contrast ratios for text and background colors
Provide text alternatives for non-text content

Website Structure
Create the following pages, with the possibility of subpages:

Home
Services
About
Contact

Specific Page Requirements
Home Page

Striking hero section with a clear value proposition
Overview of our services
Client testimonials or trust indicators

Services Page

Detailed list of our IT consulting services
Clear explanation of how we help navigate the federal IT landscape

About Page

Company history and mission
Team highlights (if applicable)
Our approach to federal IT consulting

Contact Page

Contact form
Other contact methods (phone, email)

Technical Requirements

Fully responsive design
SEO best practices implemented
Fast loading times
Integration with necessary plugins (to be discussed)
Training on how to update and maintain the site
Full compliance with Web Content Accessibility Guidelines (WCAG) 2.1 Level AA
Adherence to Section 508 standards for federal website accessibility
Implementation of necessary features for ADA compliance
Updates

Designs look the same

Target Market(s)

US Federal Govt customers looking for IT support.

Industry/Entity Type

IT Consulting

Coding

Coded - Design and coding required

Colors
0054AA
0677BA
7BADD7
CADEEF
E8F1F8
0094D4
00A9DD
6FCCEA
C7EBF8
E9F6FB
00AB8E
00BBA5
67D7C9
C6EFE9
E9F9F6

```html
<!DOCTYPE html>
<html lang="en">
<head>
<meta charset="utf-8">
<title>Brisolux Federal Services – Federal IT Consulting</title>
<link rel="stylesheet" href="https://fonts.googleapis.com/css2?family=Michroma&family=Montserrat:wght@400;500;600&display=swap">
<style>
:root{
  --brand-blue:#0094d4;
  --brand-cyan:#00a9dd;
  --brand-deep:#0677ba;
  --brand-pale:#c7ebf8;
  --ink:#1c1c1c;
  --muted:#6d6d6d;
  --dark-bg:#101820;
  --card-bg:#e6e6e6;
  --white:#ffffff;
}
*{box-sizing:border-box;margin:0;padding:0}
html,body{width:1200px;height:3132px;overflow:hidden;background:var(--white)}
body{position:relative;font-family:"Montserrat",sans-serif;color:var(--ink)}
.abs{position:absolute}
.display{font-family:"Michroma",sans-serif;text-transform:uppercase}

/* header */
.site-header{top:0;left:0;width:1200px;height:84px;background:var(--white)}
.brand{left:100px;top:26px;display:flex;align-items:center;gap:10px;font-family:"Michroma",sans-serif;font-size:22px;color:#2b3a45;white-space:nowrap}
.brand-dot{width:30px;height:30px;border-radius:50%;background:var(--brand-blue)}
.main-nav a{position:absolute;top:31px;font-size:16px;color:#333;text-decoration:none;white-space:nowrap}
.main-nav a.active{color:var(--brand-blue)}

/* hero */
.hero{top:84px;left:0;width:1200px;height:516px;background:linear-gradient(90deg,#0b7fb0 0%,#0a9ad2 55%,#0aa6e0 100%);overflow:hidden}
.hero-photo{left:711px;top:23px;width:460px;height:460px;border-radius:50%;background:radial-gradient(circle at 50% 45%,#2a7fa5 0%,#153d55 55%,#1a1a1a 78%)}
.hero .eyebrow{left:97px;top:110px;font-size:20px;color:var(--white)}
.hero h1{left:97px;top:146px;color:var(--white);font-weight:400;line-height:1}
.hero h1 .l1{display:block;font-size:38px;margin-bottom:22px}
.hero h1 .l2{display:block;font-size:56px}
.hero .lede{left:98px;top:282px;width:500px;font-size:13px;line-height:22px;color:var(--white)}
.btn{display:flex;align-items:center;justify-content:center;border-radius:30px;font-family:"Michroma",sans-serif;text-transform:uppercase;text-decoration:none;white-space:nowrap}
.btn-light{background:var(--white);color:#111}
.btn-blue{background:var(--brand-deep);color:var(--white)}
.hero .btn{left:95px;top:345px;width:176px;height:54px;font-size:13px}

/* about */
.about h2{left:98px;top:722px;font-size:25px;line-height:39px;font-weight:400;color:#111;white-space:nowrap}
.rule{height:3px;background:var(--brand-blue)}
.about .rule{left:98px;top:810px;width:98px}
.about .intro{left:98px;top:832px;width:480px;font-size:16px;line-height:26px;color:#333}
.about .detail{left:634px;width:480px;font-size:13px;line-height:21.5px;color:var(--muted)}
.about .btn{left:634px;top:885px;width:177px;height:55px;font-size:13px}

/* services */
.services{top:1035px;left:0;width:1200px;height:759px;background:radial-gradient(ellipse at 50% 40%,#1d2c3a 0%,var(--dark-bg) 75%)}
.services-strip{top:1794px;left:0;width:1200px;height:9px;background:var(--brand-pale)}
.section-title{left:0;width:1200px;text-align:center;font-size:28px;font-weight:400}
.services .section-title{top:76px;color:var(--white)}
.services .rule{left:552px;top:117px;width:96px}
.card{width:324px;height:310px;background:var(--card-bg);border-radius:14px;text-align:center}
.card.featured{background:var(--white)}
.card h3{position:absolute;left:0;width:100%;top:112px;font-family:"Michroma",sans-serif;font-weight:400;font-size:15px;text-transform:uppercase;white-space:nowrap;color:#111}
.card p{position:absolute;left:24px;width:276px;top:150px;font-size:13.5px;line-height:21.5px;color:var(--muted)}
.card .btn{position:absolute;left:86px;bottom:-23px;width:153px;height:46px;font-size:11.5px}
.portrait{width:190px;height:190px;border-radius:50%;border:4px solid var(--brand-blue)}

/* partners */
.partners .section-title{top:1905px;color:#111}
.partners .rule{left:552px;top:1946px;width:96px}
.partner-tile{top:1994px;width:242px;height:106px;background:var(--white);box-shadow:0 2px 8px rgba(0,0,0,.12);display:flex;align-items:center;justify-content:center}
.partner-tile.selected{border-top:4px solid var(--brand-deep)}
.badge{width:120px;height:44px;border-radius:8px;background:#d9e7ef}

/* contact */
.contact{top:2213px;left:0;width:1200px;height:517px;background:linear-gradient(90deg,#0a8fc6 0%,#0aa0dc 100%);overflow:hidden}
.contact-photo{left:18px;top:24px;width:462px;height:462px;border-radius:50%;background:radial-gradient(circle at 50% 45%,#8a6a5a 0%,#4a3e48 55%,#1e1e1e 80%)}
.contact h2{left:518px;top:58px;font-family:"Michroma",sans-serif;font-weight:400;font-size:26px;color:var(--white)}
.contact .rule{left:520px;top:104px;width:94px;background:var(--white)}
.contact .lede{left:521px;top:130px;width:580px;font-size:16.5px;line-height:26px;color:var(--white)}
.field{width:298px;height:57px;background:var(--white);border-radius:4px;padding:0 14px;display:flex;align-items:center;font-size:18px;color:#222}
.contact .btn{left:523px;top:399px;width:151px;height:41px;font-size:12.5px;text-transform:none;background:var(--brand-cyan);color:var(--white)}

/* footer */
.footer-brand{top:2842px;left:0;width:1200px;text-align:center;font-family:"Michroma",sans-serif;font-size:34px;color:#2b3a45;white-space:nowrap}
.footer-nav a{position:absolute;top:2962px;font-size:18px;color:#222;text-decoration:none;white-space:nowrap}
.copyright{top:3033px;left:0;width:1200px;text-align:center;font-family:"Michroma",sans-serif;font-size:14px;color:#222}
</style>
</head>
<body>

<header class="site-header abs">
  <div class="brand abs"><span class="brand-dot"></span>Brisolux</div>
  <nav class="main-nav">
    <a class="active" style="left:470px" href="#">Home</a>
    <a style="left:570px" href="#">About Us</a>
    <a style="left:694px" href="#">Our Services</a>
    <a style="left:843px" href="#">Trusted Partner</a>
    <a style="left:1017px" href="#">Contact Us</a>
  </nav>
</header>

<section class="hero abs">
  <div class="hero-photo abs" role="img" aria-label="Hand holding a glowing IT consulting hologram with technology icons"></div>
  <p class="eyebrow abs display">Welcome to</p>
  <h1 class="abs display"><span class="l1">Brightening</span><span class="l2">Solutions</span></h1>
  <p class="lede abs">Lorem ipsum dolor sit amet, consectetur adipiscing elit, sed do eiusmod tempor incididunt ut labore et dolore magna aliqua.</p>
  <a class="btn btn-light abs" href="#">Get Started</a>
</section>

<section class="about">
  <h2 class="abs display">Our company specializes<br>in federal IT consulting</h2>
  <div class="rule abs"></div>
  <p class="intro abs">Lorem ipsum dolor sit amet, consectetur adipiscing elit, sed do eiusmod tempor incididunt ut labore et dolore magna aliqua. Ut enim ad minim veniam</p>
  <p class="detail abs" style="top:692px">Lorem ipsum dolor sit amet, consectetur adipiscing elit, sed do eiusmod tempor incididunt ut labore et dolore magna aliqua. Ut enim ad minim veniam Lorem ipsum dolor sit amet, consectetur adipiscing elit, sed do eiusmod tempor incididunt ut labore et</p>
  <p class="detail abs" style="top:802px">Lorem ipsum dolor sit amet, consectetur adipiscing elit, sed do eiusmod tempor incididunt ut labore et dolore magna aliqua. Ut enim ad minim veniam Lorem ipsum dolor sit amet</p>
  <a class="btn btn-blue abs" href="#">Read More</a>
</section>

<section class="services abs">
  <h2 class="section-title abs display">Our Services</h2>
  <div class="rule abs"></div>

  <article class="card abs" style="left:98px;top:326px">
    <h3>Strategy Consultancy</h3>
    <p>Sed ut perspiciatis unde omnis iste natus error sit voluptatem accusantium doloremque laudantium, totam rem aperiam, eaque ipsa quae ab illo inventore</p>
    <a class="btn btn-light" href="#">Read More</a>
  </article>
  <div class="portrait abs" style="left:165px;top:215px;background:linear-gradient(160deg,#a7a9a6,#3f4a55)" role="img" aria-label="Portrait of a business consultant in an office"></div>

  <article class="card featured abs" style="left:437px;top:282px">
    <h3>Prototype Factory</h3>
    <p>Sed ut perspiciatis unde omnis iste natus error sit voluptatem accusantium doloremque laudantium, totam rem aperiam, eaque ipsa quae ab illo inventore</p>
    <a class="btn btn-blue" href="#">Read More</a>
  </article>
  <div class="portrait abs" style="left:504px;top:171px;background:linear-gradient(160deg,#7f8c95,#2c3a48)" role="img" aria-label="Technician working on a vehicle wheel in a workshop"></div>

  <article class="card abs" style="left:776px;top:326px">
    <h3>Corporate Venturing</h3>
    <p>Sed ut perspiciatis unde omnis iste natus error sit voluptatem accusantium doloremque laudantium, totam rem aperiam, eaque ipsa quae ab illo inventore</p>
    <a class="btn btn-light" href="#">Read More</a>
  </article>
  <div class="portrait abs" style="left:843px;top:215px;background:linear-gradient(180deg,#e7a070,#3b4f7a 60%,#1b2b45)" role="img" aria-label="Business handshake silhouetted against a city sunset"></div>
</section>
<div class="services-strip abs"></div>

<section class="partners">
  <h2 class="section-title abs display">Trusted Partner</h2>
  <div class="rule abs"></div>
  <div class="partner-tile selected abs" style="left:97px"><div class="badge" role="img" aria-label="Partner badge"></div></div>
  <div class="partner-tile abs" style="left:350px"><div class="badge" role="img" aria-label="Partner badge"></div></div>
  <div class="partner-tile abs" style="left:604px"><div class="badge" role="img" aria-label="Partner badge"></div></div>
  <div class="partner-tile abs" style="left:858px"><div class="badge" role="img" aria-label="Partner badge"></div></div>
</section>

<section class="contact abs">
  <div class="contact-photo abs" role="img" aria-label="Smiling colleagues working together at a laptop"></div>
  <h2 class="abs">Contact Us</h2>
  <div class="rule abs"></div>
  <p class="lede abs">Lorem ipsum dolor sit amet, consectetur adipiscing elit, sed do eiusmod tempor incididunt ut labore et dolore magna aliqua.</p>
  <div class="field abs" style="left:523px;top:236px">First Name</div>
  <div class="field abs" style="left:834px;top:236px">Last Name</div>
  <div class="field abs" style="left:523px;top:308px">Email</div>
  <div class="field abs" style="left:834px;top:308px">Phone</div>
  <a class="btn abs" href="#">Submit Now</a>
</section>

<footer>
  <div class="footer-brand abs">Brisolux Federal Services</div>
  <nav class="footer-nav">
    <a style="left:213px" href="#">Home</a>
    <a style="left:336px" href="#">About Us</a>
    <a style="left:486px" href="#">Our Services</a>
    <a style="left:669px" href="#">Trusted Partner</a>
    <a style="left:882px" href="#">Contact Us</a>
  </nav>
  <p class="copyright abs">©2024 Brisolux Federal Services . All Rights Reserved.</p>
</footer>

</body>
</html>
```